Telecommunications/Power civil contractor needs business card design

Were a new telecommunications/power underground civil contractor that is looking for a new business card design. Our company colours are silver or grey and orange. Feel free to use the white background logo or the black background logo.

Target Market(s)

Local contractors, utility companies, private sector mining/energy companies, developers.

Industry/Entity Type

Telecommunications

Contact Information for Business Card

Each card will need the following info:
Persons name:
Title:
E-mail:
Phone number:
Shop Address:
Mailing Address:

Requirements
Must have
• Each card will need the following info:
• Persons name:
• Title:
• E-mail:
• Phone number:
• Shop Address:
• Mailing Address:

```html
<!DOCTYPE html>
<html lang="en">
<head>
<meta charset="UTF-8">
<title>Ridgeway Civil Works – Business Card</title>
<link href="https://fonts.googleapis.com/css2?family=Montserrat:wght@400;500;700&display=swap" rel="stylesheet">
<style>
  :root {
    --page-bg: #e9e6e1;
    --card-black: #0c0c0c;
    --card-black-soft: #2a2a2a;
    --card-white: #f4f4f4;
    --bevel-grey: #9a9a9a;
    --brand-orange: #f07a45;
    --brand-silver: #8d8d8d;
    --text-dark: #1d1d1d;
  }
  html, body {
    margin: 0;
    width: 1200px;
    height: 1022px;
    overflow: hidden;
    background: var(--page-bg);
    font-family: "Montserrat", sans-serif;
  }
  .business-card {
    position: absolute;
    left: 150px;
    top: 254px;
    width: 900px;
    height: 514px;
    border-radius: 22px;
    overflow: hidden;
    box-shadow: 0 18px 40px rgba(0,0,0,0.25);
    background: var(--card-white);
  }
  .brand-panel {
    position: absolute;
    inset: 0 0 auto 0;
    height: 282px;
    background: linear-gradient(160deg, var(--card-black-soft) 0%, var(--card-black) 45%, var(--card-black) 100%);
    border-bottom: 6px solid var(--bevel-grey);
  }
  .brand-lockup {
    position: absolute;
    left: 430px;
    top: 96px;
    display: flex;
    align-items: center;
    gap: 18px;
  }
  .brand-mark {
    width: 74px;
    height: 74px;
    border-radius: 50%;
    border: 6px solid var(--brand-silver);
    box-sizing: border-box;
  }
  .brand-name {
    font-weight: 700;
    color: var(--brand-orange);
    font-size: 30px;
    line-height: 1.15;
    letter-spacing: 1px;
    text-transform: uppercase;
  }
  .details-band {
    position: absolute;
    left: 0;
    right: 0;
    top: 288px;
    bottom: 0;
    display: flex;
    padding: 34px 56px 0 56px;
    box-sizing: border-box;
  }
  .person-block {
    width: 380px;
    color: var(--text-dark);
  }
  .person-name {
    font-size: 36px;
    font-weight: 500;
    color: var(--brand-orange);
    letter-spacing: 1px;
    margin: 0;
    text-transform: uppercase;
  }
  .person-title {
    font-size: 21px;
    margin: 4px 0 10px;
    text-align: right;
    padding-right: 48px;
  }
  .shop-address {
    font-size: 21px;
    line-height: 1.3;
    margin: 0;
    font-style: normal;
  }
  .column-divider {
    width: 3px;
    height: 120px;
    margin: 16px 38px 0 30px;
    background: linear-gradient(180deg, transparent, var(--text-dark) 30%, var(--text-dark) 70%, transparent);
  }
  .contact-block {
    color: var(--text-dark);
    font-size: 20px;
    line-height: 1.32;
  }
  .mailing-address {
    margin: 0 0 4px;
    font-style: normal;
    text-transform: uppercase;
  }
  .contact-line {
    display: flex;
    align-items: center;
    gap: 12px;
  }
  .contact-line svg {
    width: 16px;
    height: 16px;
    flex: none;
  }
</style>
</head>
<body>
  <article class="business-card">
    <section class="brand-panel">
      <div class="brand-lockup">
        <span class="brand-mark"></span>
        <span class="brand-name">Ridgeway<br>Civil Works Inc</span>
      </div>
    </section>

    <section class="details-band">
      <div class="person-block">
        <h1 class="person-name">Marlon Keats</h1>
        <p class="person-title">Director</p>
        <address class="shop-address">48 Quarry Lane<br>Fairbrook, NY 12040</address>
      </div>

      <div class="column-divider"></div>

      <div class="contact-block">
        <address class="mailing-address">PO Box 3185<br>Lakeview, CA 90211</address>
        <div class="contact-line">
          <svg viewBox="0 0 16 16"><rect x="4" y="1" width="8" height="14" rx="1.5" fill="none" stroke="#f07a45" stroke-width="1.6"/></svg>
          <span>+555 0142-3318</span>
        </div>
        <div class="contact-line">
          <svg viewBox="0 0 16 16"><path d="M3 2l3 0 1 3-2 1.5a8 8 0 0 0 4.5 4.5L11 9l3 1v3a1 1 0 0 1-1 1A11 11 0 0 1 2 3a1 1 0 0 1 1-1z" fill="#f07a45"/></svg>
          <span>+555 0187-2946</span>
        </div>
        <div class="contact-line">
          <svg viewBox="0 0 16 16"><rect x="1.5" y="3.5" width="13" height="9" fill="none" stroke="#f07a45" stroke-width="1.6"/><path d="M1.5 3.5l6.5 5 6.5-5" fill="none" stroke="#f07a45" stroke-width="1.6"/></svg>
          <span>hello@ridgewaycivil.com</span>
        </div>
        <div class="contact-line">
          <svg viewBox="0 0 16 16"><circle cx="8" cy="8" r="6.5" fill="none" stroke="#f07a45" stroke-width="1.5"/><path d="M1.5 8h13M8 1.5c-3 3.5-3 9.5 0 13M8 1.5c3 3.5 3 9.5 0 13" fill="none" stroke="#f07a45" stroke-width="1.2"/></svg>
          <span>www.ridgewaycivil.com</span>
        </div>
      </div>
    </section>
  </article>
</body>
</html>
```